Corvanth Veylor - Advanced Skincare and undetectable Makeup for Men

We are in need of a professional webpage for our company Corvanth Veylor. We help every man feel his best by looking his best. Inspired by the myth of Corvanth, we offer makeup and skincare products along with education upon their use. Our mission is to celebrate masculinity in all of its forms, regardless of age, race, sexual orientation, or assigned gender at birth.

The webpage would serve as our online store, as a place where our clients can learn about our brand, view our "How-to" video tutorials, and get product information. An online blog will also be hosted in order to keep clients up to date with news, updates, media mentions, etc.

The color schemes that we use are mostly Black and Gold, with Red accents. please keep in mind that this is a men's cosmetics line, and therefore should read powerful, sexy, confident and bold - all with a high end look and feel.

Think along the lines of brands like Lem Brisko, QDV, Belluti, etc.

our logo is included in the files attached. images and copy will be added in at a later time; hence, general images that fit the feel and filler text is encouraged.

The products to be sold include:
a face cleanser in a pump dispenser bottle (1 size)
a mask in a round jar container (1 size)
a moisturizer in a pump container 1 size)
a concealer in a click pen with a brush applicator (3 shades)
a liquid liner pen (4 shades)
a contouring palette (2 shade options)
a setting spray (single option)

Target Market(s)

Millennial Men

Industry/Entity Type

Beauty

Number of Pages Required

5+ page

Font styles to use
Serif

Colors
ec1f27
000000
faa54b

Requirements
Must have
• ur essential requirements are:
• 1) a stunning and engaging landing page that truly captures the ideals of sexuality, boldness and confidence.
• 2) an interactive and engaging online store that is easy to update / add product / information to.
• 3) Product pages supporting various toggling images of the product, a shade selection option, ingredient information, usage instructions, pricing, and a link to a "how to video" unique to each individual product.
• 4) dedicated space where all of the tutorials can be organized together
• 5) an organized Blog section, that would include a segment for a Q&A section for us to update as the brand grows, ongoing contests (that would be easily hidden if there are no contests running at the moment) as well as general news and updates segment.
• 6) an "about us" page, where our customers are able to learn about our story, inspirations, humanitarian efforts and philosophies in product contents and purity.
• 7) a contact us page, which would include social media links, contact email and telephone number as well as physical address to be updated upon launch.
• 8) discrete privacy policy, terms of use, and return policy links available at the bottom of every page
Nice to have
• 1) A posting forum where clients could post their looks using our products, or maybe a live stream of our Pictoval account.
• 2) a member sign in page so that we can collect and store customer information for faster check out, keep track of purchases attached to their email address (future loyalty program plans) and maintain an email database for email notifications and the such.

```html
<!DOCTYPE html>
<html lang="en">
<head>
<meta charset="utf-8">
<title>Corvanth Veylor — Skincare &amp; Makeup</title>
<link href="https://fonts.googleapis.com/css2?family=Cinzel:wght@400;600&family=Roboto:ital,wght@0,400;0,500;0,700;1,400;1,700&display=swap" rel="stylesheet">
<style>
:root{
  --gold:#e0a21c;
  --gold-soft:#faa54b;
  --red:#ec1f27;
  --black:#000;
  --ink:#141112;
  --panel:#f0eff0;
  --text:#333;
  --muted:#777;
  --white:#fff;
}
*{margin:0;padding:0;box-sizing:border-box}
html,body{width:1200px;height:3015px;overflow:hidden}
body{position:relative;font-family:"Roboto",Arial,sans-serif;background:var(--ink);color:var(--text)}
.serif{font-family:"Cinzel",Georgia,serif}
a{color:inherit;text-decoration:none}

/* utility bar */
.utility-bar{position:absolute;top:0;left:0;width:1200px;height:40px;background:var(--gold);color:var(--white);font-size:13px;display:flex;align-items:center;justify-content:space-between;padding:0 100px 0 98px;z-index:5}
.utility-bar span.sep{margin:0 14px}
.utility-bar .account{display:flex;gap:0;align-items:center}
.utility-bar svg{width:11px;height:11px;fill:#fff;margin-right:5px;vertical-align:-1px}

/* hero */
.hero{position:absolute;top:40px;left:0;width:1200px;height:620px;background:var(--panel)}
.hero-visual{position:absolute;inset:0;clip-path:polygon(0 0,100% 0,100% 486px,594px 596px,0 490px);
  background:radial-gradient(ellipse 420px 380px at 300px 230px,#8a5a3a 0%,#4a2c1e 40%,transparent 75%),
             radial-gradient(ellipse 300px 220px at 760px 150px,rgba(230,170,60,.35),transparent 70%),
             linear-gradient(90deg,#1d1410 0%,#120c0a 55%,#0b0708 100%)}
.hero-edge{position:absolute;left:0;top:0}
.site-header{position:absolute;top:40px;left:0;width:1200px;height:110px;z-index:4}
.brand{position:absolute;left:100px;top:22px;display:flex;flex-direction:column;align-items:center;gap:8px}
.brand-mark{width:34px;height:34px;border:2px solid var(--gold)}
.brand-name{font-family:"Cinzel",Georgia,serif;font-size:13px;letter-spacing:3px;color:var(--gold)}
.main-nav{position:absolute;right:98px;top:46px;display:flex;gap:28px;align-items:center;color:var(--white);font-size:14px;font-weight:500}
.main-nav svg{width:14px;height:14px;stroke:#fff;fill:none;stroke-width:2.4}
.hero-copy{position:absolute;left:640px;top:190px;width:520px;color:var(--white);z-index:3}
.hero-copy h1{font-family:"Cinzel",Georgia,serif;font-weight:400;font-size:40px;letter-spacing:3px;line-height:1}
.hero-copy p{margin-top:28px;font-size:17px;line-height:26px;width:520px}
.btn-outline{display:inline-flex;align-items:center;gap:6px;margin-top:20px;width:168px;height:48px;justify-content:center;border:2px solid var(--white);font-size:15px;font-weight:700}
.arrow-dot{display:inline-block;width:14px;height:14px;border-radius:50%;background:currentColor;position:relative}
.arrow-dot::after{content:"";position:absolute;left:3px;top:4px;width:5px;height:5px;border-top:2px solid var(--dot,#000);border-right:2px solid var(--dot,#000);transform:rotate(45deg)}
.btn-outline .arrow-dot{--dot:#1a1210}

/* about */
.about{position:absolute;top:660px;left:0;width:1200px;height:440px;background:var(--panel)}
.about h2{position:absolute;left:98px;top:62px;font-family:"Cinzel",Georgia,serif;font-weight:400;font-size:35px;letter-spacing:3px;color:#111}
.about p{position:absolute;left:98px;top:134px;width:532px;font-size:12.5px;line-height:23.5px;color:#666}
.btn-red{display:inline-flex;align-items:center;justify-content:center;gap:6px;background:var(--red);color:var(--white);font-weight:700;font-size:14px}
.about .btn-red{position:absolute;left:98px;top:296px;width:162px;height:44px}
.btn-red .arrow-dot{--dot:var(--red)}
.video{position:absolute;left:688px;top:76px;width:414px;height:266px;background:linear-gradient(120deg,#5a4a44 0%,#a98268 45%,#c9a07a 70%,#6d5648 100%)}
.play{position:absolute;left:180px;top:114px;width:54px;height:38px;border-radius:10px;background:var(--red)}
.play::after{content:"";position:absolute;left:21px;top:11px;border-left:15px solid #fff;border-top:8px solid transparent;border-bottom:8px solid transparent}

/* category grid */
.categories{position:absolute;top:1100px;left:0;width:1200px;height:590px}
.tile{position:absolute;overflow:hidden}
.tile h3{position:absolute;left:55px;top:42px;font-family:"Cinzel",Georgia,serif;font-weight:600;font-size:28px;letter-spacing:3px;color:var(--white)}
.tile .view{position:absolute;left:55px;top:90px;color:var(--white);font-size:14px;font-weight:700;display:flex;align-items:center;gap:5px}
.tile .view .arrow-dot{--dot:#444}
.t-cleanser{left:0;top:0;width:444px;height:295px;background:linear-gradient(100deg,#2e3136 0%,#5b6068 45%,#cfd2d6 100%)}
.t-liner{left:444px;top:0;width:756px;height:295px;background:radial-gradient(ellipse 190px 140px at 300px 170px,#2a2a2d 0%,#5b4a46 55%,transparent 80%),linear-gradient(90deg,#8c6d63 0%,#b8978a 50%,#6b5a55 100%)}
.t-liner h3,.t-liner .view{left:64px}
.t-moist{left:0;top:295px;width:400px;height:295px;background:linear-gradient(110deg,#7d6a55 0%,#c6a98c 50%,#8e7a68 100%)}
.t-conceal{left:400px;top:295px;width:398px;height:295px;background:linear-gradient(110deg,#a37f68 0%,#c9a893 55%,#7e5f50 100%)}
.t-mask{left:798px;top:295px;width:402px;height:295px;background:radial-gradient(ellipse 140px 110px at 200px 210px,#e7e4de 0%,#a8a39a 60%,transparent 85%),linear-gradient(100deg,#3b3733,#7a736b 60%,#c2a650 100%)}
.t-moist h3,.t-conceal h3,.t-mask h3,.t-moist .view,.t-conceal .view,.t-mask .view{left:56px}

/* dark content */
.dark{position:absolute;top:1690px;left:0;width:1200px;height:1256px;background:radial-gradient(ellipse 700px 500px at 600px 300px,#2a2422 0%,#161213 70%),#161213}
.dark .btn-red{position:absolute;left:486px;top:50px;width:228px;height:48px}
.rule{position:absolute;left:98px;top:200px;width:1004px;height:1px;background:#777}
.section-title{position:absolute;left:0;top:272px;width:1200px;text-align:center;font-family:"Cinzel",Georgia,serif;font-weight:400;font-size:36px;letter-spacing:4px;color:var(--white)}
.post{position:absolute;top:372px;width:310px;height:378px;background:var(--white);border:3px solid var(--white)}
.post-img{position:absolute;left:0;top:0;width:304px;height:200px}
.date{position:absolute;left:0;top:136px;width:50px;height:64px;color:var(--white);font-family:"Cinzel",Georgia,serif;text-align:center;font-weight:600;padding-top:6px}
.date b{display:block;font-size:22px;line-height:26px}
.date small{font-size:12px}
.date.gold{background:var(--gold)}
.date.red{background:var(--red)}
.post h4{position:absolute;left:22px;top:228px;font-size:16px;font-weight:700;color:#222}
.post p{position:absolute;left:22px;top:264px;width:262px;font-size:12px;line-height:22px;color:#777}
.post .meta{position:absolute;left:22px;top:338px;width:262px;font-size:10.5px;color:#666;display:flex;align-items:center}
.meta i{display:inline-block;width:9px;height:9px;border-radius:50%;background:var(--gold);margin-right:6px}
.meta .bar{margin:0 8px}
.meta .more{margin-left:auto;color:var(--red);font-style:italic;font-weight:700;font-size:12px}
.p1{left:100px}.p2{left:446px}.p3{left:792px}
.p1 .post-img{background:linear-gradient(120deg,#2b1c18 0%,#8d6a58 45%,#d7b49d 70%,#1a1413 100%)}
.p2 .post-img{background:linear-gradient(120deg,#dedcd9 0%,#c7b6a8 45%,#8a6f5f 65%,#ebe9e6 100%)}
.p3 .post-img{background:linear-gradient(120deg,#b9b19c 0%,#e9e1cd 45%,#c7ac8c 70%,#8d8f6e 100%)}

.newsletter-title{position:absolute;left:0;top:838px;width:1200px;text-align:center;font-family:"Cinzel",Georgia,serif;font-weight:600;font-size:20px;letter-spacing:2.5px;color:var(--white)}
.news-line{position:absolute;left:0;top:928px;width:1200px;height:2px;background:#6b1316}
.news-form{position:absolute;left:306px;top:900px;width:586px;height:56px;border:2px solid var(--red);border-radius:28px;background:#161213;overflow:hidden;display:flex}
.news-form span{flex:1;color:#ddd;font-style:italic;font-size:14px;padding:18px 0 0 24px}
.news-form b{width:168px;background:var(--red);color:var(--white);font-size:16px;display:flex;align-items:center;justify-content:center;font-weight:700}

.footer-cols{position:absolute;top:1020px;left:0;width:1200px}
.col{position:absolute;top:0}
.col h5{font-size:16px;font-weight:700;color:var(--white);margin-bottom:22px}
.col li{list-style:none;color:#ddd;font-size:12.5px;line-height:24px;padding-left:30px;position:relative}
.col li::before{content:"»";position:absolute;left:2px;color:#fff;font-size:13px}
.c1{left:96px}.c2{left:382px}.c3{left:688px}.c4{left:900px}

.copyright{position:absolute;top:2946px;left:0;width:1200px;height:69px;background:var(--gold);color:var(--white);font-size:14px;font-weight:500;display:flex;align-items:center;justify-content:center}
</style>
</head>
<body>

<div class="utility-bar">
  <div>Complimentary Shipping &amp; Returns<span class="sep">|</span>Store Location</div>
  <div class="account">
    <span><svg viewBox="0 0 10 10"><rect x="1" y="4" width="8" height="6"/><path d="M3 4V2.5a2 2 0 0 1 4 0V4" stroke="#fff" fill="none"/></svg>Log In</span><span class="sep">|</span>
    <span><svg viewBox="0 0 10 10"><circle cx="5" cy="3" r="2.5"/><path d="M0 10a5 5 0 0 1 10 0z"/></svg>Register</span><span class="sep">|</span>
    <span><svg viewBox="0 0 10 10"><path d="M0 1h2l1.5 6h5L10 3H3"/><circle cx="4" cy="9" r="1"/><circle cx="8" cy="9" r="1"/></svg>My Cart</span>
  </div>
</div>

<section class="hero">
  <div class="hero-visual" role="img" aria-label="Model blowing golden sparkles from her open palm against a dark backdrop"></div>
  <svg class="hero-edge" width="1200" height="620" viewBox="0 0 1200 620" aria-hidden="true">
    <polygon points="0,490 594,596 1200,486 1200,500 594,612 0,504" fill="#f2b21e"/>
  </svg>
  <div class="hero-copy">
    <h1>CORVANTH VEYLOR</h1>
    <p>At vero eos et accusamus et iusto dignissimos ducimus qui blanditiis praesentium voluptatum deleniti</p>
    <a class="btn-outline" href="#">READ MORE <span class="arrow-dot"></span></a>
  </div>
</section>

<header class="site-header">
  <div class="brand"><span class="brand-mark"></span><span class="brand-name">CORVANTH VEYLOR</span></div>
  <nav class="main-nav">
    <a>HOME</a><a>ABOUT</a><a>PRODUCTS</a><a>HOW TO USE</a><a>BLOG</a><a>CONTACT</a>
    <svg viewBox="0 0 14 14"><circle cx="6" cy="6" r="4.5"/><path d="M9.5 9.5L13 13"/></svg>
  </nav>
</header>

<section class="about">
  <h2>ABOUT CORVANTH VEYLOR</h2>
  <p>At vero eos et accusamus et iusto odio dignissimos ducimus qui blanditiis praesentium voluptatum deleniti atque corrupti quos dolores et quas molestias excepturi sint occaecati cupiditate non provident, similique sunt in culpa qui officia deserunt mollitia animi, id est laborum et dolorum fuga. Et harum quidem rerum facilis est et expedita distinctio. Nam libero tempore, cum soluta nobis est elig cumque nihuo minus id quod maxime...</p>
  <a class="btn-red" href="#">READ MORE <span class="arrow-dot"></span></a>
  <div class="video" role="img" aria-label="How-to video still: makeup artist applying product to a client"><span class="play"></span></div>
</section>

<section class="categories">
  <div class="tile t-cleanser" role="img" aria-label="Person washing face at a bathroom mirror"><h3>FACE CLEANSER</h3><span class="view">VIEW ALL <span class="arrow-dot"></span></span></div>
  <div class="tile t-liner" role="img" aria-label="Close-up of an eye with liquid liner pen"><h3>LIQUID LINER PEN</h3><span class="view">VIEW ALL <span class="arrow-dot"></span></span></div>
  <div class="tile t-moist" role="img" aria-label="Person applying moisturizer in a mirror"><h3>MOISTURIZER</h3><span class="view">VIEW ALL <span class="arrow-dot"></span></span></div>
  <div class="tile t-conceal" role="img" aria-label="Hands holding a concealer palette and brush"><h3>CONCEALER</h3><span class="view">VIEW ALL <span class="arrow-dot"></span></span></div>
  <div class="tile t-mask" role="img" aria-label="Open jar of face mask cream"><h3>FACE MASK</h3><span class="view">VIEW ALL <span class="arrow-dot"></span></span></div>
</section>

<section class="dark">
  <a class="btn-red" href="#">VIEW ALL PRODUCTS <span class="arrow-dot"></span></a>
  <div class="rule"></div>
  <h2 class="section-title">LATEST BLOG POST</h2>

  <article class="post p1">
    <div class="post-img" role="img" aria-label="Model applying mascara"></div>
    <div class="date gold"><b>11</b><small>JUL</small></div>
    <h4>Shrinking From Toil and Pain</h4>
    <p>Dignissimos et ducimus atque qui blanditiis praesentium voluptatum deleniti et quas.</p>
    <div class="meta"><i></i>Dale Morrow<span class="bar">|</span><i></i>0 Comments<span class="more">More »</span></div>
  </article>
  <article class="post p2">
    <div class="post-img" role="img" aria-label="Person at a desk with makeup brushes"></div>
    <div class="date red"><b>05</b><small>JUL</small></div>
    <h4>Expound The Actual Teachings</h4>
    <p>Dignissimos et ducimus atque qui blanditiis praesentium voluptatum deleniti et quas.</p>
    <div class="meta"><i></i>Dale Morrow<span class="bar">|</span><i></i>0 Comments<span class="more">More »</span></div>
  </article>
  <article class="post p3">
    <div class="post-img" role="img" aria-label="Friends wearing face masks"></div>
    <div class="date gold"><b>08</b><small>JUL</small></div>
    <h4>Great Explorer Of The Truth</h4>
    <p>Dignissimos et ducimus atque qui blanditiis praesentium voluptatum deleniti et quas.</p>
    <div class="meta"><i></i>Dale Morrow<span class="bar">|</span><i></i>0 Comments<span class="more">More »</span></div>
  </article>

  <h2 class="newsletter-title">SIGN UP TO OUR NEWSLETTER TO STAY UPDATED</h2>
  <div class="news-line"></div>
  <div class="news-form"><span>Your Email Address Here...</span><b>SUBSCRIBE</b></div>

  <footer class="footer-cols">
    <div class="col c1"><h5>CUSTOMER CARE</h5><ul><li>Contact Us</li><li>Size Guide</li><li>My Order</li><li>My Account</li><li>Payment</li><li>Authenticity</li></ul></div>
    <div class="col c2"><h5>SHIPPING &amp; RETURNS</h5><ul><li>Payment</li><li>Save cards</li><li>Shipping</li><li>Return</li><li>Check Out</li></ul></div>
    <div class="col c3"><h5>COMPANY</h5><ul><li>About Us</li><li>Careers</li><li>Reseller</li><li>Blog Post</li></ul></div>
    <div class="col c4"><h5>LEGAL AREA</h5><ul><li>Terms and conditions of Sale</li><li>Privacy Policy</li><li>Track your order</li></ul></div>
  </footer>
</section>

<div class="copyright">© Copyright 2018 Corvanth Veylor. All Rights Reserved.</div>

</body>
</html>
```